Thornbury Building Company - Card Design

I am looking to use the logo designs that you already did for me to develop a business card. I would like the card to have a black background and be double sided. I want white and green logo and text. I have attached an inspiration photo of a look that I like. I would like to use the Vertical Logo attached to take up the full front side of the card. On the back where I have my name and information, I would like to have the horizontal logo or maybe even just the image of the 'A' and trees without the text. I am open, but I am looking for something clean and simple and I want the green to really pop! Additional files can be found under Design #: 58302946

Target Market(s)

Homeowners

Industry/Entity Type

Construction

Contact Information for Business Card

Name: Marcus Thornbury, Title: Project Manager, Phone: 555.274.8136, Email: thornburybuildingcompany@mailvesta.com, address: 487 Larkspur Ln, Ashmere, WA 95033, Lic# 2468317

Colors
00AB8E
00BBA5
67D7C9
C6EFE9
E9F9F6

Requirements
Nice to have
• I would like to see the logos that I have already got from ArtLoomHub, though I am open to new ones

```html
<!DOCTYPE html>
<html lang="en">
<head>
<meta charset="utf-8">
<title>Thornbury Building Company – Business Card</title>
<link href="https://fonts.googleapis.com/css2?family=Arimo:wght@400;700&display=swap" rel="stylesheet">
<style>
  :root {
    --stage: #2b2b2b;
    --card: #1b1b1b;
    --card-edge: #141414;
    --green: #5dbb3f;
    --white: #f2f2f2;
    --muted: #d8d8d8;
  }
  * { margin: 0; padding: 0; box-sizing: border-box; }
  html, body {
    width: 1200px; height: 801px; overflow: hidden;
    background: var(--stage);
    font-family: "Arimo", Arial, sans-serif;
  }
  .stage {
    width: 1200px; height: 801px;
    display: flex; align-items: center; justify-content: center; gap: 44px;
  }
  .card {
    position: relative;
    width: 540px; height: 309px;
    background: linear-gradient(160deg, #222 0%, var(--card) 55%, var(--card-edge) 100%);
    border-bottom: 3px solid var(--green);
    box-shadow: 0 14px 30px rgba(0,0,0,.45);
    overflow: hidden;
  }

  /* Contact side */
  .brand-lockup {
    position: absolute; left: 36px; top: 128px; width: 190px;
    display: flex; align-items: center; gap: 10px;
  }
  .brand-lockup .mark {
    flex: none; width: 22px; height: 22px; background: var(--green);
  }
  .brand-lockup .name {
    font-weight: 700; font-size: 15px; line-height: 1.2;
    color: var(--white); letter-spacing: .5px; text-transform: uppercase;
  }
  .divider {
    position: absolute; left: 248px; top: 64px;
    width: 1px; height: 170px; background: var(--green);
  }
  .contact {
    position: absolute; left: 268px; top: 66px; right: 14px;
    color: var(--muted);
  }
  .contact .person {
    font-weight: 700; font-size: 19px; color: var(--green);
    text-transform: uppercase; letter-spacing: .3px; white-space: nowrap;
  }
  .contact .role { font-size: 13px; margin-top: 4px; color: var(--white); }
  .contact .license { font-size: 12px; color: var(--green); margin-top: 16px; }
  .contact .address { font-size: 12px; margin-top: 3px; white-space: nowrap; }
  .contact ul { list-style: none; margin-top: 14px; }
  .contact li {
    display: flex; align-items: center; gap: 7px;
    font-size: 11.5px; margin-top: 6px; white-space: nowrap;
  }
  .contact li svg { flex: none; width: 11px; height: 11px; fill: var(--green); }

  /* Brand side */
  .wordmark {
    position: absolute; left: 0; right: 0; top: 92px; text-align: center;
    font-weight: 700; color: var(--white); text-transform: uppercase;
  }
  .wordmark .line-1 { font-size: 48px; letter-spacing: 3px; }
  .wordmark .line-2 { font-size: 18px; letter-spacing: 7px; margin-top: 4px; }
</style>
</head>
<body>
<main class="stage">

  <section class="card card--contact" aria-label="Card contact side">
    <div class="brand-lockup">
      <span class="mark"></span>
      <span class="name">Thornbury Building Company</span>
    </div>
    <div class="divider"></div>
    <div class="contact">
      <p class="person">Marcus Thornbury</p>
      <p class="role">Project Manager</p>
      <p class="license">Lic# 2468317</p>
      <p class="address">487 Larkspur Ln, Ashmere, WA 95033</p>
      <ul>
        <li>
          <svg viewBox="0 0 24 24" aria-hidden="true"><path d="M6.6 10.8a15.1 15.1 0 0 0 6.6 6.6l2.2-2.2a1 1 0 0 1 1-.25 11.4 11.4 0 0 0 3.6.57 1 1 0 0 1 1 1V20a1 1 0 0 1-1 1A17 17 0 0 1 3 4a1 1 0 0 1 1-1h3.5a1 1 0 0 1 1 1c0 1.25.2 2.45.57 3.57a1 1 0 0 1-.25 1z"/></svg>
          555.274.8136
        </li>
        <li>
          <svg viewBox="0 0 24 24" aria-hidden="true"><path d="M2 5h20v14H2z M2 5l10 8 10-8" fill="none" stroke="#5dbb3f" stroke-width="2.4"/></svg>
          thornburybuildingcompany@mailvesta.com
        </li>
      </ul>
    </div>
  </section>

  <section class="card card--brand" aria-label="Card brand side">
    <div class="wordmark">
      <p class="line-1">Thornbury</p>
      <p class="line-2">Building Company</p>
    </div>
  </section>

</main>
</body>
</html>
```